Business Card Design Project

Business Card
We are rebranding with a new logo
Industry/Entity Type
Business
Contact Information for Business Card
Dennis Morvale +61 487215963 dennis@quorv.com.au P.O. Box 872 Fernlow QLD 4309
Requirements
Must have
- Logo

```html
<!DOCTYPE html>
<html lang="en">
<head>
<meta charset="utf-8">
<title>Quorv International – Business Card</title>
<link rel="stylesheet" href="https://fonts.googleapis.com/css2?family=Roboto:wght@400;500;700&display=swap">
<style>
  :root {
    --backdrop: #2b2b2b;
    --card-paper: #f2f2f2;
    --brand-blue: #137aa6;
    --blue-light: #1ea6d8;
    --blue-deep: #0b5777;
    --blue-shadow: #083f58;
    --accent-orange: #f0861e;
    --text-white: #ffffff;
  }
  * { margin: 0; padding: 0; box-sizing: border-box; }
  html, body {
    width: 1200px;
    height: 960px;
    overflow: hidden;
    background: var(--backdrop);
    font-family: "Roboto", Arial, sans-serif;
  }
  .business-card {
    position: absolute;
    left: 223px;
    top: 265px;
    width: 754px;
    height: 430px;
    border-radius: 18px;
    background: var(--card-paper);
    overflow: hidden;
  }
  .card-swoosh {
    position: absolute;
    inset: 0;
    width: 754px;
    height: 430px;
  }
  .brand-name {
    position: absolute;
    left: 46px;
    top: 62px;
    width: 260px;
    font-size: 40px;
    font-weight: 500;
    line-height: 1.15;
    letter-spacing: 1px;
    color: var(--brand-blue);
  }
  .contact-block {
    position: absolute;
    right: 51px;
    top: 236px;
    text-align: right;
    color: var(--text-white);
  }
  .person-name {
    font-size: 25px;
    font-weight: 700;
    color: var(--accent-orange);
    text-transform: uppercase;
    letter-spacing: 0.2px;
    margin-bottom: 14px;
  }
  .contact-line {
    display: flex;
    justify-content: flex-end;
    align-items: center;
    gap: 7px;
    font-size: 16.5px;
    font-weight: 400;
    line-height: 24px;
  }
  .contact-line.address { margin-top: 6px; }
  .contact-icon {
    width: 15px;
    height: 15px;
    fill: var(--accent-orange);
    flex: none;
  }
</style>
</head>
<body>
  <div class="business-card">
    <svg class="card-swoosh" viewBox="0 0 754 430" aria-hidden="true">
      <defs>
        <radialGradient id="panelGradient" cx="500" cy="200" r="330" gradientUnits="userSpaceOnUse">
          <stop offset="0" stop-color="var(--blue-light)"/>
          <stop offset="1" stop-color="var(--blue-deep)"/>
        </radialGradient>
      </defs>
      <path class="swoosh-orange" d="M238 430 C330 225 500 95 660 62 C520 110 370 230 268 430 Z" fill="var(--accent-orange)"/>
      <path class="swoosh-shadow" d="M262 430 C355 232 510 100 754 38 L754 430 Z" fill="var(--blue-shadow)"/>
      <path class="swoosh-panel" d="M284 430 C380 240 535 108 754 46 L754 430 Z" fill="url(#panelGradient)"/>
    </svg>

    <div class="brand-name">Quorv International</div>

    <div class="contact-block">
      <div class="person-name">Dennis Morvale</div>
      <div class="contact-line">+61 487215963
        <svg class="contact-icon" viewBox="0 0 24 24"><path d="M6.6 10.8a15 15 0 0 0 6.6 6.6l2.2-2.2c.3-.3.7-.4 1-.2 1.1.4 2.3.6 3.6.6.6 0 1 .4 1 1V20c0 .6-.4 1-1 1A17 17 0 0 1 3 4c0-.6.4-1 1-1h3.5c.6 0 1 .4 1 1 0 1.3.2 2.5.6 3.6.1.3 0 .7-.2 1z"/></svg>
      </div>
      <div class="contact-line">dennis@quorv.com.au
        <svg class="contact-icon" viewBox="0 0 24 24"><path d="M2 5h20v14H2z M2 5l10 7 10-7" /><path d="M3 6.5l9 6.3 9-6.3V5H3z" fill="var(--blue-deep)"/></svg>
      </div>
      <div class="contact-line">www.quorv.com.au
        <svg class="contact-icon" viewBox="0 0 24 24"><circle cx="12" cy="12" r="10"/><path d="M7 8c2 0 3 1 3 3s2 2 2 4-1 3-1 5M14 4c0 2 2 3 4 3" stroke="var(--blue-deep)" stroke-width="1.6" fill="none"/></svg>
      </div>
      <div class="contact-line address">P.O. Box 872, Fernlow QLD 4309
        <svg class="contact-icon" viewBox="0 0 24 24"><path d="M12 1a8 8 0 0 0-8 8c0 6 8 14 8 14s8-8 8-14a8 8 0 0 0-8-8zm0 11a3 3 0 1 1 0-6 3 3 0 0 1 0 6z"/></svg>
      </div>
    </div>
  </div>
</body>
</html>
```